Retail Package for Ammunition Company

We are looking for a packaging design for a retail boxed ammunition. The "look". Attached will be the logo to be used. The logo is attached and a can be manipulated on the box. Box to represent strength and accuracy. Will need to provide .psd files to allow in house personnel to add/remove text to other calibers and warnings. Wow me with your designs!

Browse Other Brands: http://www.brightfalconsupply.com/brands

The packaging needs to include:
Logo- provided and the following text:

FRONT 1. 9mm 115gr FMJ

BACK 2. WARNING: To avoid serious injury: (1) use only ammunition in good condition; use only in modern firearms in good condition marked for .22 Long Rifle (LR) cartridges; (2) always be sure barrel is free of any obstructions; the barrel should be checked in case of light recoil, or an unusually loud or weak sound heard during firing; (3) wear eye and ear protection; (4) if gun fails to fire, avoid exposure to breech when unloading and point muzzle in a safe direction. Keep firearm pointed in safe direction at all times; (5) discharge may occur if rim is struck; handle with caution, do not drop. (6) Do not shoot at hard surfaces or water to prevent ricochet; (7) Bullet is capable of traveling extreme distances. Know your backstop; (8) Store in cool dry place

3. LEAD WARNING: Discharging firearms in poorly ventilated areas, cleaning firearms, or handling ammunition may result in exposure to lead and other substances known to cause birth defects, reproductive harm, and other serious physical injury. Have adequate ventilation at all times. Wash hands thoroughly after exposure.

Dimensions ; (LxWxH): 5.25" x 2.625" x 1.125"

Target Market(s)

Ammunition Industry

```html
<!DOCTYPE html>
<html lang="en">
<head>
<meta charset="utf-8">
<title>Ember Crest Armory – 9mm 115gr FMJ Retail Box</title>
<link href="https://fonts.googleapis.com/css2?family=Source+Sans+3:wght@400;600;700&display=swap" rel="stylesheet">
<style>
  :root {
    --red-deep: #5e0406;
    --red-mid: #a90a10;
    --red-bright: #e0262c;
    --silver-dark: #555a5f;
    --silver-light: #d6d8da;
    --white: #ffffff;
    --paper: #f4f4f4;
    --stage: #e9e9ea;
    --brand-red: #8c1116;
    --ink: #1c1c1c;
  }
  * { margin: 0; padding: 0; box-sizing: border-box; }
  html, body { width: 1200px; height: 750px; overflow: hidden; }
  body {
    background: var(--stage);
    font-family: "Source Sans 3", "Myriad Pro", Arial, sans-serif;
    position: relative;
  }
  .panel { position: absolute; overflow: hidden; }
  .red-field {
    background: radial-gradient(ellipse at 55% 45%, var(--red-bright) 0%, var(--red-mid) 45%, var(--red-deep) 100%);
  }

  /* Top face */
  .top-face { left: 240px; top: 30px; width: 920px; height: 197px; }
  .top-face .brand-lockup {
    position: absolute; left: 270px; top: 62px;
    display: flex; align-items: center; gap: 26px;
  }
  .brand-name {
    font-weight: 700; letter-spacing: 2px; text-transform: uppercase;
    display: flex; align-items: center; gap: 10px;
  }
  .brand-name .dot { width: 14px; height: 14px; border-radius: 50%; background: currentColor; }
  .top-face .brand-name { color: var(--white); font-size: 34px; line-height: 1; }
  .top-face .descriptor {
    color: var(--white); font-weight: 700; font-size: 18px; letter-spacing: 1.5px;
    line-height: 1.25; text-transform: uppercase;
  }

  /* End panel */
  .end-panel { left: 30px; top: 237px; width: 197px; height: 460px; background: var(--white); }
  .end-panel .red-top { position: absolute; left: 0; top: 0; width: 100%; height: 300px; }
  .end-panel .silver-band {
    position: absolute; left: 0; top: 300px; width: 100%; height: 26px;
    background: linear-gradient(180deg, var(--silver-dark), var(--silver-light));
  }
  .end-panel .brand-name {
    position: absolute; left: 0; top: 128px; width: 100%; justify-content: center;
    color: var(--white); font-size: 19px;
  }
  .end-panel .caliber {
    position: absolute; left: 0; top: 352px; width: 100%; text-align: center; color: var(--ink);
  }
  .caliber .load { font-size: 36px; font-weight: 700; line-height: 1; }
  .caliber .type { font-size: 14px; font-weight: 700; text-transform: uppercase; line-height: 1.25; margin-top: 8px; }

  /* Back panel */
  .back-panel { left: 240px; top: 237px; width: 920px; height: 460px; background: var(--white); }
  .back-panel svg.swoosh { position: absolute; left: 0; top: 0; }
  .warnings {
    position: absolute; left: 60px; top: 38px; width: 810px; color: var(--white);
  }
  .warning-block { font-size: 19px; line-height: 1.28; }
  .warning-block + .warning-block { margin-top: 26px; font-size: 17px; }
  .warning-title { font-weight: 700; font-size: 30px; letter-spacing: 0.5px; }
  .back-panel .brand-name {
    position: absolute; left: 470px; top: 376px;
    color: var(--brand-red); font-size: 38px; line-height: 1;
  }
</style>
</head>
<body>

  <section class="panel top-face red-field" aria-label="Top face">
    <div class="brand-lockup">
      <div class="brand-name"><span class="dot"></span>Ember Crest Armory</div>
      <div class="descriptor">Full Metal Jacket<br>FMJ / Elite Ammunition</div>
    </div>
  </section>

  <section class="panel end-panel" aria-label="End panel">
    <div class="red-top red-field"></div>
    <div class="silver-band"></div>
    <div class="brand-name"><span class="dot"></span>Ember Crest</div>
    <div class="caliber">
      <div class="load">9mm 115gr</div>
      <div class="type">Full Metal Jacket<br>FMJ / Elite Ammunition</div>
    </div>
  </section>

  <section class="panel back-panel" aria-label="Back panel">
    <svg class="swoosh" width="920" height="460" viewBox="0 0 920 460" aria-hidden="true">
      <defs>
        <radialGradient id="backRed" cx="55%" cy="40%" r="70%">
          <stop offset="0" stop-color="#e0262c"/>
          <stop offset="0.45" stop-color="#a90a10"/>
          <stop offset="1" stop-color="#5e0406"/>
        </radialGradient>
        <linearGradient id="silver" x1="0" y1="0" x2="0" y2="1">
          <stop offset="0" stop-color="#4d5257"/>
          <stop offset="1" stop-color="#d6d8da"/>
        </linearGradient>
      </defs>
      <path d="M0 0 H920 V318 H520 L470 330 Q300 370 0 420 Z" fill="url(#backRed)"/>
      <path d="M0 420 Q300 370 470 330 L520 318 H920 V350 H530 L480 358 Q300 395 0 445 Z" fill="url(#silver)"/>
    </svg>

    <div class="warnings">
      <p class="warning-block"><span class="warning-title">LEAD WARNING:</span> Discharging firearms in poorly ventilated areas, cleaning firearms, or handling ammunition may result in exposure to lead and other substances known to cause birth defects, reproductive harm, and other serious physical injury. Have adequate ventilation at all times. Wash hands thoroughly after exposure.</p>
      <p class="warning-block"><span class="warning-title">WARNING:</span> To avoid serious injury: (1) use only ammunition in good condition; use only in modern firearms in good condition marked for .22 Long Rifle (LR) cartridges; (2) always be sure barrel is free of any obstructions; the barrel should be checked in case of light recoil, or an unusually loud or weak sound heard during firing; (3) wear eye and ear protection; (4) if gun fails to fire, avoid exposure to breech when unloading and point muzzle in a safe direction. Keep firearm pointed in safe direction at all times; (5) discharge may occur if rim is struck; handle with caution, do not drop. (6) Do not shoot at hard surfaces or water to prevent ricochet; (7) Bullet is capable of traveling extreme distances. Know your backstop; (8) Store in cool dry place</p>
    </div>

    <div class="brand-name"><span class="dot"></span>Ember Crest Armory</div>
  </section>

</body>
</html>
```